Dog Snacks brand needs a new packaging design

Dear Designers,

We are looking for a packaging expert to design our new line of Dog Snacks which contain a relaxing hemp extract (CBD).

Our company is already selling various relaxing cat & dog products , and we would like this new design to reflect the same "style & feeling" as our current products (see attached instructions).

Technical aspects:
- The packaging is a Stand Up Pouch (12x18.5x7cm - see attached instructions).
- Please follow technical guidelines from printer (see attached instructions).
- The packaging will contain 120g of high-quality, semi-moist dog snacks.
- We will be designing 3 differents variations for 3 different flavours: Chicken, Beef & Liver.
- The packaging will be printed with a matt finish.

Design aspects:
- The design should be compatible with our brand identity (i.e. fluffly, pure, relaxing, positive, clean & natural).
- Soft/rounded shapes are preferred.
- Please use our brand's colors (#3BA384, White & Black).
- Please use our company logo (see attached instructions).
- The design also needs to convey a strong sense of professionalism as we are an animal "healthcare" brand.
- If you want to include a dog picture, we would prefer you to use a picture of our official brand ambassador (see attached instructions).
- We have attached a number of packaging examples which we like a lot. (see attached instructions). Please only use those as general inspiration.
- Only original work (no plagiarism will be accepted).

Please don't hesitate to send us a message if you have any questions about the brand, the product or the design requirements.

We look forward to seeing your designs & working on this together !

Thanks & regards,
Tobias

Target Market(s)

Dog owners

Industry/Entity Type

Pet Care

Font styles to use
Sans Serif

Requirements
Must have
• Please see project description.
Nice to have
Should not have

```html
<!DOCTYPE html>
<html lang="en">
<head>
<meta charset="utf-8">
<title>VERDALO CBD Treats – Chicken Flavour</title>
<link rel="stylesheet" href="https://fonts.googleapis.com/css2?family=Montserrat:wght@300;400;600;700&family=Roboto+Condensed:wght@300;400&display=swap">
<style>
  :root {
    --brand-green: #3BA384;
    --band-green: #67B39D;
    --ink: #231F20;
    --white: #FFFFFF;
    --photo-light: #F1F1F0;
    --photo-mid: #D9D6D3;
  }
  * { margin: 0; padding: 0; box-sizing: border-box; }
  html, body { width: 740px; height: 1200px; overflow: hidden; background: var(--white); }
  .pouch {
    position: relative; width: 740px; height: 1200px; overflow: hidden;
    background: var(--white); font-family: "Montserrat", sans-serif; color: var(--ink);
  }
  .brand-tab {
    position: absolute; left: 252px; top: 0; width: 236px; height: 351px;
    background: var(--brand-green); border-radius: 0 0 48px 48px;
  }
  .brand-name {
    position: absolute; left: 0; right: 0; top: 244px; text-align: center;
    font-family: "Montserrat", sans-serif; font-weight: 400; font-size: 36px;
    letter-spacing: 1px; color: var(--white); line-height: 1;
  }
  .brand-sub {
    position: absolute; right: 20px; top: 282px; font-family: "Montserrat", sans-serif;
    font-weight: 400; font-size: 14px; color: var(--white); line-height: 1;
  }
  .thc-free { position: absolute; left: 592px; top: 120px; color: var(--brand-green); line-height: 1; }
  .thc-free .thc { display: block; font-weight: 700; font-size: 42px; letter-spacing: -1px; }
  .thc-free .free { display: block; font-weight: 300; font-size: 33px; margin-top: 2px; }
  .product-title { position: absolute; left: 50px; top: 396px; line-height: 1; }
  .product-title .cbd { display: block; font-weight: 600; font-size: 144px; color: var(--brand-green); letter-spacing: -4px; }
  .product-title .treats { display: block; margin-top: 12px; margin-left: 6px; font-weight: 700; font-size: 76px; letter-spacing: 0.17em; color: var(--ink); }
  .divider { position: absolute; left: 62px; top: 635px; width: 275px; height: 4px; background: var(--brand-green); }
  .dose { position: absolute; left: 60px; top: 660px; font-weight: 700; font-size: 35px; line-height: 1; letter-spacing: -1px; }
  .dose .label { color: var(--brand-green); margin-right: 6px; }
  .vet-claim {
    position: absolute; left: 64px; top: 752px; font-family: "Roboto Condensed", sans-serif;
    font-weight: 300; font-size: 30px; line-height: 30px; color: var(--brand-green);
  }
  .vet-icon { position: absolute; left: 222px; top: 746px; }
  .flavour { position: absolute; left: 64px; top: 856px; line-height: 1; }
  .flavour .name { display: block; font-weight: 700; font-size: 27px; letter-spacing: -1px; }
  .flavour .word { display: block; font-weight: 300; font-size: 21px; margin-top: 1px; }
  .flavour-icon { position: absolute; left: 172px; top: 856px; }
  .net-weight {
    position: absolute; left: 64px; top: 936px; font-family: "Roboto Condensed", sans-serif;
    font-weight: 400; font-size: 52px; line-height: 1; color: var(--brand-green);
  }
  .hero { position: absolute; left: 0; top: 0; }
  .line-name {
    position: absolute; left: 194px; top: 1006px; font-family: "Roboto Condensed", sans-serif;
    font-weight: 300; font-size: 92px; line-height: 1; color: var(--brand-green); letter-spacing: -2px;
  }
  .line-name sup { font-size: 22px; vertical-align: top; position: relative; top: 14px; margin-left: 4px; letter-spacing: 0; }
  .benefit-band {
    position: absolute; left: 0; top: 1097px; width: 740px; height: 103px; background: var(--band-green);
  }
  .benefit-band p {
    position: absolute; left: 196px; top: 21px; font-weight: 600; font-size: 19px;
    letter-spacing: 0.26em; color: var(--white); white-space: nowrap;
  }
</style>
</head>
<body>
<main class="pouch">
  <svg class="hero" width="740" height="1200" viewBox="0 0 740 1200">
    <defs>
      <linearGradient id="photo-tone" x1="0" y1="0" x2="1" y2="1">
        <stop offset="0" stop-color="var(--photo-light)"/>
        <stop offset="0.6" stop-color="var(--photo-mid)"/>
        <stop offset="1" stop-color="var(--photo-light)"/>
      </linearGradient>
    </defs>
    <ellipse cx="640" cy="900" rx="350" ry="310" fill="var(--brand-green)"/>
    <ellipse role="img" aria-label="Photo of the brand's white wrinkled dog looking up at a blue butterfly on its nose" cx="650" cy="920" rx="337" ry="275" fill="url(#photo-tone)"/>
  </svg>

  <header class="brand-tab">
    <span class="brand-name">VERDALO</span>
    <span class="brand-sub">For Animals</span>
  </header>

  <div class="thc-free"><span class="thc">THC</span><span class="free">FREE</span></div>

  <h1 class="product-title"><span class="cbd">CBD</span><span class="treats">TREATS</span></h1>
  <div class="divider"></div>
  <p class="dose"><span class="label">CBD</span>250MG</p>

  <p class="vet-claim">Recommended<br>by Veterinarians</p>
  <svg class="vet-icon" width="52" height="86" viewBox="0 0 52 86" fill="none" stroke="var(--brand-green)" stroke-width="3" stroke-linecap="round">
    <path d="M26 48 C8 34 4 24 8 14 C12 6 22 6 26 14 C30 6 42 6 46 14 C50 24 44 34 26 48"/>
    <path d="M26 48 C34 58 40 70 34 78 C28 84 18 80 20 72"/>
    <circle cx="17" cy="66" r="5"/>
    <circle cx="26" cy="28" r="4" fill="var(--brand-green)" stroke="none"/>
  </svg>

  <div class="flavour"><span class="name">CHICKEN</span><span class="word">FLAVOUR</span></div>
  <svg class="flavour-icon" width="58" height="54" viewBox="0 0 58 54" fill="none" stroke="var(--ink)" stroke-width="2.5" stroke-linecap="round" stroke-linejoin="round">
    <path d="M20 30 C14 18 22 4 36 3 C50 2 58 14 52 24 C46 32 32 34 24 34 Z"/>
    <path d="M22 32 L12 42"/>
    <circle cx="9" cy="42" r="3.5"/>
    <circle cx="13" cy="47" r="3.5"/>
  </svg>

  <p class="net-weight">120g</p>

  <p class="line-name">VerdaBites<sup>TM</sup></p>

  <footer class="benefit-band"><p>SUPPORT | CALM | EASE</p></footer>
</main>
</body>
</html>
```